Plakat-Design für Vereinsfest
Zielgruppe
Unser Verein veranstaltet jedes Jahr im August das Vereinsfest 'Mühlentanz', das in einem kleinen Wäldchen innerhalb des Heimatortes stattfindet. Am Samstag und Sonntag sorgen verschiedene Musikgruppen für Unterhaltung. Es soll ein Veranstaltungsplakat gestaltet werden, dass sich an die Vorgaben (siehe unten) hält und die Veranstaltung bewirbt.
Zielgruppe sind Bürger des Heimatortes.
Aufgabenstellung
Das Vereinslogo ist beigefügt und sollte prominent auf dem Plakat vertreten sein, Logo und Schriftzug können auch getrennt oder anders angeordnet werden. Der Veranstaltungstitel lautet "Mühlentanz", es findet am 20. und 21. August "Am Rinkelsteig" (Veranstaltungsort) statt.
Programmpunkte: Samstag: Musikalische Unterhaltung mit den Hopfenbläsern; Sonntag: Musikalische Unterhaltung mit den Kieselgrubenrabauken
Uhrzeiten sollten enthalten sein:
Beginn Samstag: ab 15 Uhr
Beginn Sonntag: ab 10 Uhr
Das Plakat soll gut leserlich auch aus der Entfernung sein, da es an Straßen plakatiert wird.
Das Plakat soll für spätere Jahre editierbar sein.
Schriftart im Logo: Californian FB Bold (muss aber nicht auf andere Textelemente angewendet werden). Das Plakat soll in DIN A2 gedruckt werden. Die Webadresse sollte auf dem Plakat stehen.

```html
<!DOCTYPE html>
<html lang="de">
<head>
<meta charset="utf-8">
<title>Mühlentanz – Plakat</title>
<link rel="stylesheet" href="https://fonts.googleapis.com/css2?family=Abril+Fatface&family=Libre+Caslon+Text:wght@400;700&display=swap">
<style>
  :root {
    --stage: #e9e8e6;
    --paper: #f4f2f0;
    --blue: #155a85;
    --navy: #1d2a6b;
    --grey-text: #3e3e3e;
    --grey-box: #4d4d4d;
    --ornament-tint: #c9d8e3;
    --white: #ffffff;
  }
  * { box-sizing: border-box; margin: 0; padding: 0; }
  html, body { width: 1200px; height: 1178px; overflow: hidden; background: var(--stage); }
  body { position: relative; font-family: "Libre Caslon Text", Georgia, serif; }

  .poster {
    position: absolute; left: 200px; top: 24px;
    width: 800px; height: 1130px;
    background: var(--paper);
    box-shadow: 0 2px 10px rgba(0,0,0,.12);
  }
  .border-outer, .border-inner {
    position: absolute; border: 3px solid var(--blue); pointer-events: none;
  }
  .border-outer { inset: 16px; }
  .border-inner { inset: 25px; border-width: 1.5px; }

  .corner-ornament {
    position: absolute; width: 120px; height: 120px;
    background: linear-gradient(135deg, var(--ornament-tint), rgba(201,216,227,0) 75%);
  }
  .corner-ornament.tl { left: 32px; top: 32px; }
  .corner-ornament.tr { right: 32px; top: 32px; transform: scaleX(-1); }
  .corner-ornament.bl { left: 32px; bottom: 32px; transform: scaleY(-1); }
  .corner-ornament.br { right: 32px; bottom: 32px; transform: scale(-1,-1); }

  .club-name {
    position: absolute; left: 160px; top: 80px; width: 500px;
    display: flex; align-items: center; gap: 22px;
  }
  .club-name .mark {
    width: 110px; height: 110px; border-radius: 50%;
    background: var(--navy); flex: none;
  }
  .club-name p {
    color: var(--navy); font-weight: 400; font-size: 25px; line-height: 1.12;
  }

  .event-title {
    position: absolute; left: 0; right: 0; top: 246px;
    text-align: center;
  }
  .event-title h1 {
    display: inline-block;
    font-family: "Abril Fatface", "Didot", serif; font-weight: 400;
    font-size: 84px; line-height: 1; color: var(--blue);
    letter-spacing: -1px;
    transform: scaleY(1.45); transform-origin: top center;
  }

  .date-band {
    position: absolute; left: 58px; right: 58px; top: 398px; height: 124px;
    background: var(--blue); color: var(--white); text-align: center;
    padding-top: 10px;
  }
  .date-band .dates { font-weight: 700; font-size: 52px; line-height: 1.1; }
  .date-band .venue { font-weight: 400; font-size: 36px; line-height: 1.2; }

  .programme {
    position: absolute; left: 90px; right: 70px; top: 545px;
    display: flex; justify-content: space-between; text-align: center;
  }
  .programme .day { width: 300px; }
  .programme .day:first-child { margin-top: 10px; }
  .programme h2 { font-size: 30px; font-weight: 700; color: var(--grey-text); line-height: 1.05; }
  .programme p { font-size: 25px; font-weight: 700; color: var(--blue); line-height: 1.3; }

  .start-times {
    position: absolute; left: 220px; width: 385px; top: 700px; height: 100px;
    background: var(--grey-box); color: var(--white);
    font-size: 26px; line-height: 1.3; text-align: center;
    display: flex; flex-direction: column; justify-content: center;
  }

  .gallery {
    position: absolute; left: 245px; top: 840px; width: 410px; height: 190px;
  }
  .gallery .portrait {
    position: absolute; left: 0; bottom: 0; width: 110px; height: 185px;
    background: linear-gradient(180deg, #8e8e8e, #4a4a4a);
    border-radius: 55px 55px 0 0;
  }
  .gallery .photo-slot {
    position: absolute; bottom: 10px; width: 110px; height: 150px;
    border: 2px solid #222; background: var(--paper);
    display: flex; align-items: center; justify-content: center;
    font-weight: 700; font-size: 20px; color: #222;
  }
  .gallery .photo-slot.one { left: 140px; }
  .gallery .photo-slot.two { left: 285px; }
  .gallery .base {
    position: absolute; left: 100px; right: 0; bottom: 0; height: 10px; background: var(--grey-box);
  }

  .web-address {
    position: absolute; left: 0; right: 0; top: 1052px; text-align: center;
    font-size: 27px; font-weight: 700; color: var(--grey-text);
  }
</style>
</head>
<body>
<main class="poster">
  <div class="border-outer"></div>
  <div class="border-inner"></div>
  <div class="corner-ornament tl" role="img" aria-label="Verzierte Eckornamente in Blau"></div>
  <div class="corner-ornament tr" role="img" aria-label="Verzierte Eckornamente in Blau"></div>
  <div class="corner-ornament bl" role="img" aria-label="Verzierte Eckornamente in Blau"></div>
  <div class="corner-ornament br" role="img" aria-label="Verzierte Eckornamente in Blau"></div>

  <header class="club-name">
    <span class="mark"></span>
    <p>Historische Schützengilde und Trachtenverein Ebersried e.V.</p>
  </header>

  <div class="event-title"><h1>MÜHLENTANZ</h1></div>

  <section class="date-band">
    <div class="dates">20 - 21 August</div>
    <div class="venue">“Am Rinkelsteig”</div>
  </section>

  <section class="programme">
    <div class="day">
      <h2>SAMSTAG:</h2>
      <p>Musikalische Unterhaltung mit den Hopfenbläsern</p>
    </div>
    <div class="day">
      <h2>SONNTAG:</h2>
      <p>Musikalische Unterhaltung mit den Kieselgrubenrabauken</p>
    </div>
  </section>

  <section class="start-times">
    <span>Beginn Samstag: ab 15 Uhr</span>
    <span>Beginn Sonntag: ab 10 Uhr</span>
  </section>

  <section class="gallery">
    <div class="portrait" role="img" aria-label="Figur in Tracht mit Radhaube, schwarz-weiß"></div>
    <div class="base"></div>
    <div class="photo-slot one">Foto</div>
    <div class="photo-slot two">Foto</div>
  </section>

  <footer class="web-address">www.schuetzengilde-ebersried.de</footer>
</main>
</body>
</html>
```